Wedding Videography Wordpress Website Theme

We need a modern and high-end website look for our wedding video and film business. We film weddings all over the United Kingdom and at European destinations so need something to reflect our work. The website should be visually stunning with images and videos being the focal point as this is what our services are.

The current website is www.brunolessway.com so you will be able to see our brand.

My Instagram is www.instagram.com/brunolesswayfilms so a new design should link in with this idea.

We need the following pages designed by the winning designer

1 - Homepage
2 - Films Index Page
3 - Testimonials
4 - Prices
5 - Reviews
6 - Meet Bruno (About)
7 - Contact
8 - Blog Index
9 - Blog Page

All pages must be consistent so have a similar style.

Pages on menu:
Meet Bruno
Videos
Packages
Testimionials
Journal (Blog)
Contact

We require a responsive look too. Over 90% of our visitors access the website via their mobile devices.

```html
<!DOCTYPE html>
<html lang="en">
<head>
<meta charset="utf-8">
<title>Enquire – Bruno Lessway Wedding Films</title>
<link href="https://fonts.googleapis.com/css2?family=Cormorant+Garamond:wght@500;600&family=Jost:wght@300;400;500&display=swap" rel="stylesheet">
<style>
:root{
  --board:#efefef;
  --white:#ffffff;
  --gold:#a88a45;
  --gold-dark:#8e7436;
  --cream:#f6edcf;
  --cream-soft:#f7f0e3;
  --sand:#e5d6ac;
  --button:#e0cf9f;
  --ink:#2b2b2b;
  --muted:#8b8b8b;
  --field-line:#e6e2d8;
  --panel:#f7f7f6;
  --quote-mark:#e8e0ce;
}
*{box-sizing:border-box;margin:0;padding:0}
html,body{width:1200px;height:2179px;overflow:hidden;background:var(--board)}
body{font-family:"Jost",sans-serif;color:var(--ink);position:relative}
.a{position:absolute}
.serif{font-family:"Cormorant Garamond",serif;font-weight:600;color:var(--gold);text-transform:uppercase;letter-spacing:.04em}
.center{text-align:center}

.desktop{position:absolute;left:179px;top:0;width:697px;height:1921px;background:var(--white);overflow:hidden}
.mobile{position:absolute;left:925px;top:0;width:164px;height:2179px;background:var(--white);overflow:hidden}

.photo-hero{background:linear-gradient(160deg,#6f6a58 0%,#8e8460 35%,#b9a57a 55%,#6b6a4a 80%,#4c4a3a 100%)}
.photo-hero::after{content:"";position:absolute;inset:0;background:rgba(30,28,20,.25)}
.brand{font-family:"Jost",sans-serif;font-weight:500;color:var(--white);letter-spacing:.18em;text-transform:uppercase;z-index:2}
.brand-gold{color:var(--gold)}
.nav{z-index:2;font-size:7px;font-weight:500;color:var(--white);text-transform:uppercase;letter-spacing:.03em}
.nav-btn{z-index:2;background:var(--button);color:var(--ink);font-size:7px;font-weight:500;display:flex;align-items:center;justify-content:center;text-transform:uppercase}
.hero-title{z-index:2;color:#e9d9a8;font-family:"Cormorant Garamond",serif;font-weight:600;letter-spacing:.04em}
.hero-sub{z-index:2;color:var(--white);font-weight:500}

.contact-card{background:var(--cream);display:flex;align-items:center}
.contact-card .label{font-size:6.5px;color:#555}
.contact-card .value{font-weight:500;color:var(--ink)}
.intro{font-size:7.5px;line-height:15px;color:#555}
.intro b{color:var(--ink);font-weight:500}

.photo-house{background:linear-gradient(180deg,#c9d0d6 0%,#b5bcbc 18%,#6f6b5a 30%,#8a7c62 50%,#5f7c3c 62%,#6f9a3c 100%)}
.form-panel{background:var(--panel)}
.field{background:var(--white);border:1px solid var(--field-line);font-size:6.5px;color:var(--muted);display:flex;align-items:center;justify-content:space-between;padding:0 11px}
.field.tall{align-items:flex-start;padding-top:10px}
.btn-gold{background:var(--button);font-weight:500;display:flex;align-items:center;justify-content:center;color:var(--ink)}

.band-testimonials{background:var(--cream-soft)}
.photo-couple-a{background:linear-gradient(170deg,#8fa07a,#4b5a3f 45%,#2f3a55 70%,#e8e6e0 100%)}
.photo-couple-b{background:linear-gradient(160deg,#1e2a1d 0%,#4f5646 35%,#7d7a70 60%,#66635a 100%)}
.photo-couple-c{background:linear-gradient(170deg,#3a2e25 0%,#6b5a48 40%,#d8d2c8 65%,#2e3550 100%)}
.play{border-radius:50%;background:rgba(255,255,255,.85);display:flex;align-items:center;justify-content:center;z-index:2}
.arrow-box{display:flex;align-items:center;justify-content:center}
.quote-mark{font-family:"Cormorant Garamond",serif;font-weight:600;color:var(--quote-mark);font-size:60px;line-height:1}
.quote{font-size:8px;line-height:16px;color:#3a3a3a}
.attrib{font-size:7.5px;font-weight:500;color:var(--gold);display:flex;align-items:center;justify-content:center;gap:10px}
.attrib .rule{width:14px;height:1px;background:var(--gold)}

.band-instagram{background:var(--sand)}
.insta-title{font-family:"Cormorant Garamond",serif;font-weight:500;color:#6f5f38;letter-spacing:.3em;text-transform:uppercase}
.tile-1{background:linear-gradient(170deg,#d7c9b4,#8c7a66 60%,#3b3a3a)}
.tile-2{background:linear-gradient(160deg,#4a4e5c,#a9a39a 50%,#f0ece6)}
.tile-3{background:linear-gradient(180deg,#e9ecef 0%,#dfe3e4 45%,#9a8e6b 65%,#7d7150 100%)}
.tile-4{background:linear-gradient(160deg,#2d2b26,#8f9a79 50%,#ece9e0)}
.tile-5{background:linear-gradient(170deg,#3d4a32,#8a7b6a 50%,#e6ddd2)}
.tile-6{background:linear-gradient(180deg,#3c6fb8 0%,#8fb2df 45%,#eceff0 70%,#6b8a3d 100%)}
.btn-white{background:var(--white);font-size:7.5px;display:flex;align-items:center;justify-content:center;color:var(--ink)}

.foot-head{font-weight:500;font-size:9px;display:flex;align-items:center;gap:6px;color:var(--ink)}
.foot-head .rule{width:12px;height:1px;background:#999}
.foot-item{font-size:7px;color:#444;display:flex;align-items:center;gap:10px}
.social{display:flex;gap:8px}
.social span{width:13px;height:11px;border:1px solid var(--gold);border-radius:2px}
.copy{font-size:6px;color:#999}
</style>
</head>
<body>

<main class="desktop">

  <section class="a photo-hero" style="left:0;top:0;width:697px;height:358px" role="img" aria-label="Bride laughing with friends outdoors on a windy day"></section>
  <div class="a brand" style="left:69px;top:38px;font-size:10px">Bruno Lessway</div>
  <nav>
    <div class="a nav" style="left:230px;top:47px">Meet Bruno</div>
    <div class="a nav" style="left:296px;top:47px">Videos</div>
    <div class="a nav" style="left:347px;top:47px">Packages</div>
    <div class="a nav" style="left:412px;top:47px">Testimonials</div>
    <div class="a nav" style="left:487px;top:47px">Journal</div>
    <div class="a nav-btn" style="left:546px;top:37px;width:84px;height:26px">Enquire</div>
  </nav>
  <h1 class="a hero-title center" style="left:0;width:697px;top:172px;font-size:22px">ENQUIRE</h1>
  <div class="a hero-sub center" style="left:0;width:697px;top:204px;font-size:9px">Contact me today</div>

  <h2 class="a serif center" style="left:0;width:697px;top:395px;font-size:16px">Ready for a chat?</h2>
  <div class="a contact-card" style="left:140px;top:440px;width:201px;height:62px">
    <svg class="a" style="left:28px;top:17px" width="30" height="30" viewBox="0 0 30 30" fill="none" stroke="#a88a45" stroke-width="1.2"><path d="M8 3l4 6-3 3c1 4 5 8 9 9l3-3 6 4-3 5C12 26 4 18 3 7z"/><path d="M17 6a7 7 0 0 1 7 7M17 2a11 11 0 0 1 11 11"/></svg>
    <div class="a label" style="left:78px;top:17px">Call Me:</div>
    <div class="a value" style="left:78px;top:32px;font-size:11px">07700 900123</div>
  </div>
  <div class="a contact-card" style="left:353px;top:440px;width:199px;height:62px">
    <svg class="a" style="left:18px;top:16px" width="32" height="30" viewBox="0 0 32 30" fill="none" stroke="#a88a45" stroke-width="1.2"><path d="M2 12h28v16H2z"/><path d="M2 12l14 10 14-10"/><path d="M7 14V3h15l4 4v7"/><path d="M11 8h8M11 11h8"/><circle cx="24" cy="6" r="3"/></svg>
    <div class="a label" style="left:69px;top:17px">Email Me:</div>
    <div class="a value" style="left:69px;top:32px;font-size:10.5px">films@brunolessway.com</div>
  </div>
  <p class="a intro center" style="left:102px;top:521px;width:478px">I’ll respond in a couple of hours or so.Before enquiring please check my prices to see if I am within your budget. <b>Click here for my packages.</b>We can chat about your wedding plans, check my availability, and see if we’re a match made in heaven.</p>

  <div class="a photo-house" style="left:66px;top:587px;width:277px;height:375px" role="img" aria-label="Aerial view of a stately stone manor house with wedding guests on the lawn"></div>
  <section class="a form-panel" style="left:343px;top:587px;width:285px;height:375px">
    <h2 class="a serif" style="left:28px;top:21px;font-size:16px">Get in touch</h2>
  </section>
  <div class="a field" style="left:370px;top:642px;width:238px;height:28px">How did you hear about my wedding films?
    <svg width="8" height="5" viewBox="0 0 8 5" fill="none" stroke="#aaa"><path d="M1 1l3 3 3-3"/></svg></div>
  <div class="a field" style="left:370px;top:682px;width:114px;height:28px">First name</div>
  <div class="a field" style="left:493px;top:682px;width:114px;height:28px">Last name</div>
  <div class="a field" style="left:370px;top:721px;width:114px;height:27px">Email address</div>
  <div class="a field" style="left:493px;top:721px;width:114px;height:27px">Mobile number</div>
  <div class="a field" style="left:370px;top:759px;width:238px;height:28px">When is your wedding day?
    <svg width="12" height="12" viewBox="0 0 12 12" fill="none" stroke="#aaa"><rect x="1" y="2" width="10" height="9"/><path d="M1 5h10M4 1v2M8 1v2"/></svg></div>
  <div class="a field" style="left:370px;top:799px;width:238px;height:28px">What time is your wedding ceremony?
    <svg width="12" height="12" viewBox="0 0 12 12" fill="none" stroke="#aaa"><circle cx="6" cy="6" r="5"/><path d="M6 3v3l2 2"/></svg></div>
  <div class="a field tall" style="left:370px;top:837px;width:238px;height:58px">what are you planning for your wedding day?</div>
  <div class="a btn-gold" style="left:370px;top:908px;width:114px;height:27px;font-size:8px">Submit</div>

  <section class="a band-testimonials" style="left:0;top:1014px;width:697px;height:441px">
    <h2 class="a serif center" style="left:0;width:697px;top:44px;font-size:16px">Wedding video testimonials</h2>
  </section>
  <div class="a photo-couple-a" style="left:0;top:1112px;width:137px;height:191px" role="img" aria-label="Groom kissing the bride on the cheek in a garden"></div>
  <div class="a photo-couple-b" style="left:163px;top:1099px;width:370px;height:217px" role="img" aria-label="Video still of a bride and groom walking hand in hand"></div>
  <div class="a play" style="left:335px;top:1192px;width:26px;height:26px"><svg width="9" height="10" viewBox="0 0 9 10"><path d="M1 0l8 5-8 5z" fill="#a88a45"/></svg></div>
  <div class="a arrow-box" style="left:163px;top:1293px;width:31px;height:23px;background:var(--white)"><svg width="12" height="8" viewBox="0 0 12 8" fill="none" stroke="#777"><path d="M11 4H1M4 1L1 4l3 3"/></svg></div>
  <div class="a arrow-box" style="left:502px;top:1293px;width:31px;height:23px;background:var(--button)"><svg width="12" height="8" viewBox="0 0 12 8" fill="none" stroke="#333"><path d="M1 4h10M8 1l3 3-3 3"/></svg></div>
  <div class="a photo-couple-c" style="left:558px;top:1112px;width:139px;height:191px" role="img" aria-label="Bride and groom leaving the ceremony under falling petals"></div>
  <div class="a quote-mark" style="left:160px;top:1322px">“</div>
  <p class="a quote center" style="left:192px;top:1333px;width:316px">We have a really emotional video for our wedding. It is a beauty video that is going to stay with us for the rest of our lives. Bruno was everywhere but you couldn’t tell he was there. He was a really fun guy and we now consider him a friend.”</p>
  <div class="a attrib" style="left:0;width:697px;top:1394px"><span class="rule"></span>Married at Villa Serena, Umbria, Italy<span class="rule"></span></div>

  <section class="a band-instagram" style="left:0;top:1455px;width:697px;height:271px">
    <h2 class="a insta-title center" style="left:0;width:697px;top:37px;font-size:17px">Follow me on Instagram</h2>
  </section>
  <div class="a tile-1" style="left:66px;top:1539px;width:84px;height:93px" role="img" aria-label="Couple walking down a cobbled street"></div>
  <div class="a tile-2" style="left:162px;top:1539px;width:84px;height:93px" role="img" aria-label="Groom and laughing bride under confetti"></div>
  <div class="a tile-3" style="left:258px;top:1539px;width:84px;height:93px" role="img" aria-label="Horse-drawn wedding carriage in a field"></div>
  <div class="a tile-4" style="left:354px;top:1539px;width:84px;height:93px" role="img" aria-label="Father of the bride walking her in"></div>
  <div class="a tile-5" style="left:450px;top:1539px;width:84px;height:93px" role="img" aria-label="Groom and bride smiling at each other"></div>
  <div class="a tile-6" style="left:546px;top:1539px;width:84px;height:93px" role="img" aria-label="Bridal party jumping in the air"></div>
  <div class="a btn-white" style="left:273px;top:1662px;width:150px;height:32px">Follow me @brunolesswayfilms</div>

  <footer>
    <div class="a brand brand-gold" style="left:67px;top:1800px;font-size:9.5px">Bruno Lessway</div>
    <div class="a social" style="left:89px;top:1833px"><span></span><span></span><span></span></div>
    <div class="a foot-head" style="left:240px;top:1772px">Contact <span class="rule"></span></div>
    <div class="a foot-item" style="left:240px;top:1800px"><svg width="10" height="10" viewBox="0 0 10 10" fill="none" stroke="#999"><path d="M2 1l2 2-1 1c0 1 2 3 3 3l1-1 2 2-1 1C4 9 1 6 1 2z"/></svg>07700 900123</div>
    <div class="a foot-item" style="left:240px;top:1828px"><svg width="10" height="8" viewBox="0 0 10 8" fill="none" stroke="#999"><rect x=".5" y=".5" width="9" height="7"/><path d="M1 1l4 3 4-3"/></svg>films@brunolessway.com</div>
    <div class="a foot-head" style="left:406px;top:1772px">Links <span class="rule"></span></div>
    <div class="a foot-item" style="left:408px;top:1797px">FAQ’s</div>
    <div class="a foot-item" style="left:408px;top:1817px">Wedding Photography</div>
    <div class="a foot-item" style="left:408px;top:1836px">Commercial</div>
    <div class="a foot-item" style="left:534px;top:1797px">North East Wedding Venues</div>
    <div class="a foot-item" style="left:534px;top:1817px">Free Speeches Guide</div>
    <div class="a foot-item" style="left:534px;top:1836px">Blog</div>
    <div class="a copy center" style="left:0;width:697px;top:1875px">© Copyright 2022 Bruno Lessway Films Ltd All Rights Reserved</div>
  </footer>
</main>

<main class="mobile">
  <section class="a photo-hero" style="left:0;top:0;width:164px;height:252px" role="img" aria-label="Bride laughing with friends outdoors on a windy day"></section>
  <div class="a brand" style="left:8px;top:30px;font-size:6px">Bruno Lessway</div>
  <svg class="a" style="left:141px;top:25px;z-index:2" width="13" height="10" viewBox="0 0 13 10" stroke="#fff" stroke-width="1.2"><path d="M0 1h13M0 5h13M4 9h9"/></svg>
  <h1 class="a hero-title center" style="left:0;width:164px;top:118px;font-size:17px">ENQUIRE</h1>
  <div class="a hero-sub center" style="left:0;width:164px;top:147px;font-size:7px">Contact me today</div>

  <h2 class="a serif center" style="left:0;width:164px;top:268px;font-size:11.5px">Ready for a chat?</h2>
  <div class="a contact-card" style="left:0;top:296px;width:164px;height:54px">
    <svg class="a" style="left:13px;top:14px" width="26" height="26" viewBox="0 0 30 30" fill="none" stroke="#a88a45" stroke-width="1.3"><path d="M8 3l4 6-3 3c1 4 5 8 9 9l3-3 6 4-3 5C12 26 4 18 3 7z"/><path d="M17 6a7 7 0 0 1 7 7M17 2a11 11 0 0 1 11 11"/></svg>
    <div class="a label" style="left:58px;top:14px;font-size:5.5px">Call Me:</div>
    <div class="a value" style="left:58px;top:27px;font-size:9px">07700 900123</div>
  </div>
  <div class="a contact-card" style="left:0;top:360px;width:164px;height:54px">
    <svg class="a" style="left:10px;top:13px" width="27" height="26" viewBox="0 0 32 30" fill="none" stroke="#a88a45" stroke-width="1.3"><path d="M2 12h28v16H2z"/><path d="M2 12l14 10 14-10"/><path d="M7 14V3h15l4 4v7"/><path d="M11 8h8M11 11h8"/><circle cx="24" cy="6" r="3"/></svg>
    <div class="a label" style="left:55px;top:14px;font-size:5.5px">Email Me:</div>
    <div class="a value" style="left:55px;top:27px;font-size:8.5px">films@brunolessway.com</div>
  </div>
  <p class="a intro center" style="left:12px;top:430px;width:140px;font-size:6px;line-height:13.5px">I’ll respond in a couple of hours or so. Before enquiring please check my prices to see if I am within your budget. <b>Click here for my packages.</b>We can chat about your wedding plans, check my availability, and see if we’re a match made in heaven.</p>

  <section class="a band-testimonials" style="left:0;top:523px;width:164px;height:368px">
    <h2 class="a serif center" style="left:0;width:164px;top:12px;font-size:10.5px;line-height:18px">Wedding video<br>testimonials</h2>
  </section>
  <div class="a photo-couple-b" style="left:4px;top:578px;width:155px;height:145px" role="img" aria-label="Video still of a bride and groom walking hand in hand"></div>
  <div class="a play" style="left:71px;top:642px;width:18px;height:18px"><svg width="6" height="7" viewBox="0 0 9 10"><path d="M1 0l8 5-8 5z" fill="#a88a45"/></svg></div>
  <div class="a arrow-box" style="left:4px;top:703px;width:28px;height:20px;background:var(--white)"><svg width="11" height="7" viewBox="0 0 12 8" fill="none" stroke="#777"><path d="M11 4H1M4 1L1 4l3 3"/></svg></div>
  <div class="a arrow-box" style="left:131px;top:703px;width:28px;height:20px;background:var(--button)"><svg width="11" height="7" viewBox="0 0 12 8" fill="none" stroke="#333"><path d="M1 4h10M8 1l3 3-3 3"/></svg></div>
  <p class="a quote center" style="left:8px;top:748px;width:148px;font-size:6.5px;line-height:13.8px">We have a really emotional video for our wedding. It is a beauty video that is going to stay with us for the rest of our lives. Bruno was everywhere but you couldn’t tell he was there. He was a really fun guy and we now consider him a friend.”</p>
  <div class="a attrib center" style="left:10px;width:144px;top:846px;font-size:6.5px;line-height:12px;gap:6px"><span class="rule"></span><span>Married at Villa Serena,<br>Umbria, Italy</span><span class="rule"></span></div>

  <div class="a photo-house" style="left:4px;top:902px;width:155px;height:137px" role="img" aria-label="Aerial view of a stately stone manor house with wedding guests on the lawn"></div>
  <section class="a form-panel" style="left:4px;top:1039px;width:155px;height:375px">
    <h2 class="a serif center" style="left:0;width:155px;top:14px;font-size:10.5px">Get in touch</h2>
  </section>
  <div class="a field" style="left:12px;top:1078px;width:135px;height:25px;font-size:5.5px;padding:0 7px">How did you hear about my wedding films?</div>
  <div class="a field" style="left:12px;top:1110px;width:135px;height:25px;font-size:5.5px;padding:0 7px">First name</div>
  <div class="a field" style="left:12px;top:1143px;width:135px;height:25px;font-size:5.5px;padding:0 7px">Last name</div>
  <div class="a field" style="left:12px;top:1177px;width:135px;height:25px;font-size:5.5px;padding:0 7px">Email address</div>
  <div class="a field" style="left:12px;top:1209px;width:135px;height:25px;font-size:5.5px;padding:0 7px">Mobile number</div>
  <div class="a field" style="left:12px;top:1242px;width:135px;height:25px;font-size:5.5px;padding:0 7px">When is your wedding day?
    <svg width="9" height="9" viewBox="0 0 12 12" fill="none" stroke="#aaa"><rect x="1" y="2" width="10" height="9"/><path d="M1 5h10M4 1v2M8 1v2"/></svg></div>
  <div class="a field" style="left:12px;top:1274px;width:135px;height:25px;font-size:5.5px;padding:0 7px">What time is your wedding ceremony?
    <svg width="9" height="9" viewBox="0 0 12 12" fill="none" stroke="#aaa"><circle cx="6" cy="6" r="5"/><path d="M6 3v3l2 2"/></svg></div>
  <div class="a field tall" style="left:12px;top:1309px;width:135px;height:50px;font-size:5.5px;padding:7px 7px 0">What are you planning for your wedding day?</div>
  <div class="a btn-gold" style="left:28px;top:1374px;width:101px;height:23px;font-size:7px">Submit</div>

  <section class="a band-testimonials" style="left:0;top:1426px;width:164px;height:375px">
    <h2 class="a insta-title center" style="left:0;width:164px;top:22px;font-size:11px;line-height:18px;letter-spacing:.25em">Follow me on<br>Instagram</h2>
  </section>
  <div class="a tile-2" style="left:4px;top:1498px;width:76px;height:77px" role="img" aria-label="Groom and laughing bride under confetti"></div>
  <div class="a tile-1" style="left:83px;top:1498px;width:75px;height:77px" role="img" aria-label="Couple walking down a cobbled street"></div>
  <div class="a tile-3" style="left:4px;top:1580px;width:76px;height:78px" role="img" aria-label="Horse-drawn wedding carriage in a field"></div>
  <div class="a tile-4" style="left:83px;top:1580px;width:75px;height:78px" role="img" aria-label="Father of the bride walking her in"></div>
  <div class="a tile-5" style="left:4px;top:1662px;width:76px;height:78px" role="img" aria-label="Groom and bride smiling at each other"></div>
  <div class="a tile-6" style="left:83px;top:1662px;width:75px;height:78px" role="img" aria-label="Bridal party jumping in the air"></div>
  <div class="a btn-white" style="left:15px;top:1756px;width:135px;height:28px;font-size:6.5px">Follow me @brunolesswayfilms</div>

  <footer>
    <div class="a brand brand-gold center" style="left:0;width:164px;top:1850px;font-size:8.5px">Bruno Lessway</div>
    <div class="a social" style="left:56px;top:1880px"><span></span><span></span><span></span></div>
    <div class="a foot-head" style="left:20px;top:1926px;font-size:8px">Contact <span class="rule"></span></div>
    <div class="a foot-item" style="left:20px;top:1951px;font-size:6px">07700 900123</div>
    <div class="a foot-item" style="left:20px;top:1976px;font-size:6px">films@brunolessway.com</div>
    <div class="a foot-head" style="left:20px;top:2004px;font-size:8px">Links <span class="rule"></span></div>
    <div class="a foot-item" style="left:22px;top:2026px;font-size:6px">FAQ’s</div>
    <div class="a foot-item" style="left:22px;top:2043px;font-size:6px">Wedding Photography</div>
    <div class="a foot-item" style="left:22px;top:2060px;font-size:6px">Commercial</div>
    <div class="a foot-item" style="left:22px;top:2079px;font-size:6px">North East Wedding Venues</div>
    <div class="a foot-item" style="left:22px;top:2097px;font-size:6px">Free Speeches Guide</div>
    <div class="a foot-item" style="left:22px;top:2114px;font-size:6px">Blog</div>
    <div class="a copy" style="left:22px;top:2141px;font-size:5.5px;line-height:12px">© Copyright 2022 Bruno Lessway Films Ltd.<br>All Rights Reserved.</div>
  </footer>
</main>

</body>
</html>
```